Generate website for parcelnook.com

Please design a website for our business. It must be clean, streamlined and obvious.

Our business combines ecommerce, with social networking, and zorvi maps. The logo is a shopping bag (ecommerce) and honeycombs inside representing the various compartments of business that are offered throughout site.

Clients use our site to visit the interior of stores and restaurants through video streaming and can virtually "walk through" the store and purchase items with friends and loved ones through the web.

We want to incorporate this logo with the work that we are doing and play on this honeycomb theme.

Our business is "parcelnook.com" because we are all about "u"!

Please make homepage with about us tab, contact us form, mission tab, we also want a page with our research links included that bolster the case for our startup.

We will incorporate a small video on the front screen. A homepage like fildrawer.com only this time with our parcelnook!

Also include, COMING SOON, on the homepage please.
Updates

These are some good templates/example sites of clean and simple but effective: https://7elmrow.com/preview www.fildrawer.com

We are excited to see your submissions. Currently, a very good and only one designer has posted so far. Let us know!

Please include the TM (trademark) symbol after the logo, the name, and the slogan throughout the website. Thank you!

Put the TM after the LOGO and after the slogan "Placement ran Supreme" Lorcan

Target Market(s)

We will begin with female online shoppers.

Industry/Entity Type

Shopping

Font styles to use
Serif
Sans Serif

Colors
e567a6
fece3e
85cae6

Requirements
Must have
• Clean Look
Simple like Fildrawer with simple options "see film" or login/signup.

With browser tabs at the bottom much like fildrawer.

1. Shopper when opening Parcelnook.com website will see a simple webpage with a large Parcelnook logo in the center.

2. User will see log-in and password or create account in upper right hand corner of webpage. Mobile device website will be underneath logo.

3.We Prefer a background for webpages adding a softer experience on the the eyes of the user. A photo in the background to show shopretail experience.

4. Clicking on theParcelnook logo will inform users of details and instructions about platform. Example: About, contact, mission, Help etc. Logo will become somewhat like an interactive tool for help and guidance.

5. Parcelnook is currently scouting for it's founding venues. A founding venue will be the first venues to appear to the public on the Parcelnook platform. Founding venues (FV) will inherit a lifetime of the lowest possible rates of 2%* for the duration of it's business. All businesses wishing to participate in the founding venues offer please leave your email address and store name and a representative will get back with you.

*Venues will be subjected to credit card and CoinTrail rates in addition.

Nice to have
• http://www.zorvi.com/patents/US5193774

Must include the link above/visual of this page on the site as well.

```html
<!DOCTYPE html>
<html lang="en">
<head>
<meta charset="utf-8">
<title>Parcelnook</title>
<link rel="stylesheet" href="https://fonts.googleapis.com/css2?family=Cookie&family=Jost:wght@400;500;700&family=Arimo&family=Tinos&display=swap">
<style>
  :root{
    --photo-top:#7a5a55;
    --photo-mid:#b9a7a6;
    --photo-floor:#6b4a3c;
    --panel:rgba(240,236,235,0.72);
    --band:#4d666b;
    --sky:#a2dcf1;
    --sand:#fcdc84;
    --mint:#c9e2c8;
    --white:#ffffff;
    --ink:#222222;
    --logo-ink:#5e5e60;
    --honey:#fff27a;
    --honey-deep:#f2d64a;
    --rule:#9aa6a2;
  }
  *{margin:0;padding:0;box-sizing:border-box}
  html,body{width:1200px;height:1091px;overflow:hidden}
  body{position:relative;background:var(--white);font-family:"Jost",sans-serif}
  .hero-photo{position:absolute;left:0;top:0;width:1200px;height:745px;
    background:linear-gradient(180deg,var(--photo-top) 0%,#a58a8a 14%,var(--photo-mid) 40%,#9e8a86 75%,var(--photo-floor) 100%)}
  .hero-band{position:absolute;left:0;top:745px;width:1200px;height:15px;background:var(--band)}
  .hero-panel{position:absolute;left:0;top:148px;width:1200px;height:515px;background:var(--panel);
    box-shadow:0 8px 14px rgba(0,0,0,.35)}
  .brand{position:absolute;left:0;top:220px;width:1200px;text-align:center}
  .brand-name{display:inline-flex;align-items:center;gap:16px;font-family:"Jost",sans-serif;font-weight:700;
    font-size:66px;color:var(--logo-ink);line-height:1}
  .brand-mark{width:44px;height:44px;background:var(--logo-ink);border-radius:6px}
  .tagline{position:absolute;left:0;top:337px;width:1200px;text-align:center;font-size:24px;color:var(--ink)}
  .divider{position:absolute;left:618px;top:398px;width:2px;height:240px;background:var(--white)}
  .offer{position:absolute;top:398px;width:420px;text-align:center}
  .offer--shopper{left:167px}
  .offer--venue{left:646px}
  .offer-title{font-family:"Cookie",cursive;font-size:42px;line-height:52px;color:var(--white);
    text-shadow:2px 3px 4px rgba(0,0,0,.7);font-weight:400}
  .offer-box{position:absolute;top:106px;width:380px;height:141px;border:2px solid var(--white);border-radius:10px}
  .offer--shopper .offer-box{left:22px}
  .offer--venue .offer-box{left:14px}
  .offer-hint{margin-top:10px;font-family:"Cookie",cursive;font-size:27px;color:var(--white);
    text-shadow:1px 2px 3px rgba(0,0,0,.7)}
  .cta{position:absolute;background:linear-gradient(180deg,var(--honey) 0%,var(--honey-deep) 100%);
    box-shadow:1px 2px 4px rgba(0,0,0,.6);border:2px solid #fff9c0}
  .cta--login{left:83px;top:48px;width:206px;height:56px;font-family:"Tinos",serif;font-size:34px;
    color:var(--white);text-shadow:1px 2px 3px rgba(0,0,0,.7);line-height:52px}
  .cta--email{left:83px;top:51px;width:206px;height:57px}
  .site-footer{position:absolute;left:0;top:760px;width:1200px;height:331px;
    background:linear-gradient(160deg,var(--sky) 0%,var(--sky) 30%,var(--mint) 55%,var(--sand) 100%)}
  .footer-nav{position:absolute;left:66px;top:30px;width:200px;list-style:none;text-align:center}
  .footer-nav li{font-family:"Arimo",sans-serif;font-size:27px;color:var(--white);height:59px}
  .footer-rule{position:absolute;left:63px;top:277px;width:1096px;height:1px;background:var(--rule)}
  .copyright{position:absolute;left:0;top:287px;width:1200px;text-align:center;font-size:14px;color:var(--ink)}
</style>
</head>
<body>
  <div class="hero-photo" role="img" aria-label="Soft-focus photo of a shopping mall storefront interior"></div>
  <div class="hero-band"></div>
  <div class="hero-panel"></div>

  <div class="brand"><span class="brand-name"><span class="brand-mark"></span>Parcelnook</span></div>
  <p class="tagline">Shop and walk with friends through the aisles</p>

  <div class="divider"></div>

  <section class="offer offer--shopper">
    <h2 class="offer-title">Sign up to join the<br>experience</h2>
    <div class="offer-box">
      <p class="offer-hint">Visit a store</p>
      <div class="cta cta--login">Signup/Login</div>
    </div>
  </section>

  <section class="offer offer--venue">
    <h2 class="offer-title">Request or Become a<br>participating store</h2>
    <div class="offer-box">
      <p class="offer-hint">Please leave your email</p>
      <div class="cta cta--email"></div>
    </div>
  </section>

  <footer class="site-footer">
    <ul class="footer-nav">
      <li>Coming soon</li>
      <li>About us</li>
      <li>mission</li>
      <li>Contact us</li>
    </ul>
    <div class="footer-rule"></div>
    <p class="copyright">©2014 · Parcelnook.com LLC. All rights reserved. Under authorized use of patent #5193774 Natpo</p>
  </footer>
</body>
</html>
```